Design my dad a new business card because his current one sucks!

I need a business card designed for my fathers home maintenance business. His customers are individuals (single moms, old people etc.) as well as the occasional business. As such it needs to be accessible to both target audiences.

The front of the card should be dark grey on yellow with the logo and contain the following information:
- Darren Holtwick
- 0488 274 915
- info@brightoakhomecare.com.au
- 0488 274 915

- ABN: 71 284 630 912
- 'Fully Insured'

The reverse should be yellow on dark grey and will have the web address:
- brightoakhomecare.com.au

And a few key services he offers:
GENERAL REPAIRS
PAINTING/TILING/
PAVING &CONCRETING
PRESSURE WASHING
ON-SITE WELDING
DECKING ADDITIONS & REPAIRS
FENCING
FULL BOND CLEANING

This will be first time the logo has been printed so you will need to come up with the best CMYK approximation of the RGB colours to make sure it is a close as possible.

```html
<!DOCTYPE html>
<html lang="en">
<head>
<meta charset="utf-8">
<title>Bright Oak Home Care – Business Card Reverse</title>
<link href="https://fonts.googleapis.com/css2?family=Michroma&family=Smythe&display=swap" rel="stylesheet">
<style>
  :root {
    --paper: #ffffff;
    --card-grey: #525252;
    --brand-yellow: #f6e500;
  }
  html, body {
    margin: 0;
    padding: 0;
    width: 1200px;
    height: 900px;
    overflow: hidden;
    background: var(--paper);
  }
  .canvas {
    position: relative;
    width: 1200px;
    height: 900px;
    background: var(--paper);
  }
  .card-reverse {
    position: absolute;
    left: 0;
    top: 133px;
    width: 1200px;
    height: 667px;
    background: var(--card-grey);
    color: var(--brand-yellow);
  }
  .web-address {
    position: absolute;
    left: 68px;
    top: 62px;
    margin: 0;
    font-family: "Michroma", sans-serif;
    font-weight: 400;
    font-size: 41px;
    letter-spacing: 0.5px;
    line-height: 1;
  }
  .service-list {
    position: absolute;
    left: 69px;
    top: 167px;
    margin: 0;
    padding: 0;
    list-style: none;
    font-family: "Smythe", sans-serif;
    font-size: 44px;
    line-height: 54.3px;
    text-transform: uppercase;
    letter-spacing: 0.3px;
  }
  .service-icons {
    position: absolute;
    left: 552px;
    top: 519px;
    display: flex;
    gap: 8px;
  }
  .service-icon {
    width: 76px;
    height: 76px;
    display: block;
  }
  .service-icon .disc { fill: var(--brand-yellow); }
  .service-icon .glyph { fill: var(--card-grey); }
  .service-icon .stroke { stroke: var(--card-grey); fill: none; stroke-linecap: round; }
</style>
</head>
<body>
<main class="canvas">
  <section class="card-reverse">
    <p class="web-address">brightoakhomecare.com.au</p>
    <ul class="service-list">
      <li>General Repairs</li>
      <li>Painting/Tiling/</li>
      <li>Paving &amp;Concreting</li>
      <li>Pressure Washing</li>
      <li>On-Site Welding</li>
      <li>Decking Additions &amp; Repairs</li>
      <li>Fencing</li>
      <li>Full Bond Cleaning</li>
    </ul>
    <div class="service-icons">
      <!-- paint roller -->
      <svg class="service-icon" viewBox="-38 -38 76 76" role="img" aria-label="Paint roller">
        <circle class="disc" r="38"/>
        <g transform="rotate(-40)">
          <rect class="glyph" x="-6" y="-22" width="12" height="26" rx="2"/>
          <rect class="glyph" x="-2" y="4" width="4" height="8"/>
          <rect class="glyph" x="-3.5" y="12" width="7" height="14" rx="2"/>
        </g>
      </svg>
      <!-- trowel -->
      <svg class="service-icon" viewBox="-38 -38 76 76" role="img" aria-label="Trowel">
        <circle class="disc" r="38"/>
        <path class="glyph" d="M-4 -4 L20 -20 L6 6 Z"/>
        <line class="stroke" x1="-2" y1="2" x2="-18" y2="18" stroke-width="6"/>
      </svg>
      <!-- fence -->
      <svg class="service-icon" viewBox="-38 -38 76 76" role="img" aria-label="Fence">
        <circle class="disc" r="38"/>
        <path class="glyph" d="M-20 -12 L-15 -20 L-10 -12 V20 H-20 Z M-5 -12 L0 -20 L5 -12 V20 H-5 Z M10 -12 L15 -20 L20 -12 V20 H10 Z"/>
        <rect class="glyph" x="-22" y="-4" width="44" height="4"/>
        <rect class="glyph" x="-22" y="8" width="44" height="4"/>
      </svg>
      <!-- hammer and wrench -->
      <svg class="service-icon" viewBox="-38 -38 76 76" role="img" aria-label="Hammer and wrench">
        <circle class="disc" r="38"/>
        <line class="stroke" x1="-16" y1="-12" x2="16" y2="20" stroke-width="6"/>
        <rect class="glyph" x="-24" y="-24" width="18" height="10" transform="rotate(45 -15 -19)"/>
        <line class="stroke" x1="14" y1="-14" x2="-16" y2="16" stroke-width="6"/>
        <circle class="glyph" cx="16" cy="-16" r="8"/>
        <circle class="disc" cx="20" cy="-20" r="4"/>
      </svg>
      <!-- cleaning bucket -->
      <svg class="service-icon" viewBox="-38 -38 76 76" role="img" aria-label="Cleaning bucket">
        <circle class="disc" r="38"/>
        <path class="glyph" d="M-20 -8 H20 L15 22 H-15 Z"/>
        <path class="stroke" d="M-16 -8 Q0 -28 16 -8" stroke-width="3"/>
        <rect class="glyph" x="-6" y="-22" width="6" height="14"/>
      </svg>
      <!-- welding mask -->
      <svg class="service-icon" viewBox="-38 -38 76 76" role="img" aria-label="Welding mask">
        <circle class="disc" r="38"/>
        <path class="glyph" d="M-8 -22 H12 Q20 -22 20 -10 V10 Q20 22 6 22 H-4 Q-14 22 -14 10 V-14 Q-14 -22 -8 -22 Z"/>
        <rect class="disc" x="-4" y="-10" width="16" height="8" rx="1"/>
        <path class="stroke" d="M-20 14 L-26 10 M-20 18 L-28 20 M-18 22 L-22 28" stroke-width="2"/>
      </svg>
      <!-- paint brush -->
      <svg class="service-icon" viewBox="-38 -38 76 76" role="img" aria-label="Paint brush">
        <circle class="disc" r="38"/>
        <line class="stroke" x1="20" y1="-20" x2="4" y2="-4" stroke-width="5"/>
        <path class="glyph" d="M6 -10 L10 -6 L-2 6 L-6 2 Z"/>
        <path class="stroke" d="M-3 3 L-22 22 M-1 5 L-18 24 M-5 1 L-24 18" stroke-width="1.6"/>
      </svg>
    </div>
  </section>
</main>
</body>
</html>
```